Podiatry (services) Business Card

I need a business design for a New Podiatry Service.
the Podiatry services will include all aspects of podiatry including;
general podiatry for all ages
corns and callus treatment
Ingrown toenails & nail surgery
Forefoot, arch and heel pain
Gait analysis
Sports Podiatry and Orthotics
Paediatric Assessments
Diabetes Foot Assessment

I would like the back of the card to have space for next appointment day and time.

I would like a nice design that is simple yet catchy. I don't like cluttered business cards. I like things to be simple yet stand out because of the finer details.

I like the colours blue and white but I'm open to other designs that have different colours.

Business

Bluewren Podiatry (Business name)

Marisol Tenbury - Podiatrist
M.Pod.P., B.Hlth. Sci, MFLsoc

Address: 58 Coleby St, Marrowdale North Vic, 3164
Phone: (03) 9416 2738
Fax: (03) 9523 4178

```html
<!DOCTYPE html>
<html lang="en">
<head>
<meta charset="utf-8">
<title>Bluewren Podiatry – Business Card</title>
<link href="https://fonts.googleapis.com/css2?family=Quicksand:wght@500&family=Source+Sans+3:wght@400;600&family=Tinos:wght@400;700&display=swap" rel="stylesheet">
<style>
  :root {
    --blue: #1a72aa;
    --blue-deep: #135f90;
    --grey: #6f8299;
    --ink: #4d5a68;
    --white: #ffffff;
    --backdrop: #e9edf1;
  }
  * { box-sizing: border-box; margin: 0; padding: 0; }
  html, body { width: 1200px; height: 789px; overflow: hidden; }
  body { background: var(--backdrop); position: relative; font-family: "Source Sans 3", sans-serif; }

  .card {
    position: absolute;
    width: 540px; height: 300px;
    border-radius: 4px;
    overflow: hidden;
    box-shadow: 0 8px 22px rgba(30, 50, 70, .18);
  }
  .card__shape { position: absolute; inset: 0; width: 100%; height: 100%; }

  /* ---------- Brand block ---------- */
  .brand {
    position: absolute;
    display: flex; align-items: center; gap: 14px;
    font-family: "Quicksand", sans-serif; font-weight: 500;
  }
  .brand__dot { width: 26px; height: 26px; border-radius: 50%; flex: none; }
  .brand__name { font-size: 34px; line-height: 1.05; }
  .brand__line { display: block; }

  /* ---------- Back: services + appointment ---------- */
  .card--back { left: 60px; top: 100px; background: var(--blue); }

  .card--back .brand { left: 56px; top: 76px; color: var(--white); }
  .card--back .brand__dot { border: 2px solid var(--white); }

  .services {
    position: absolute; left: 292px; top: 26px;
    padding-left: 18px;
    border-left: 1px solid rgba(255,255,255,.8);
    list-style: none; color: var(--white);
    font-size: 13px; line-height: 16.5px;
  }
  .services li { display: flex; align-items: center; gap: 7px; }
  .services li::before {
    content: ""; width: 0; height: 0;
    border-left: 7px solid var(--white);
    border-top: 4px solid transparent; border-bottom: 4px solid transparent;
  }

  .appointment { position: absolute; left: 0; right: 0; bottom: 0; height: 110px; color: var(--blue); }
  .appointment__title {
    position: absolute; left: 70px; top: 46px;
    font-family: "Quicksand", sans-serif; font-weight: 500; font-size: 18px;
  }
  .appointment__field {
    position: absolute; font-size: 14px;
    display: flex; align-items: flex-end; gap: 6px;
  }
  .appointment__field::after { content: ""; border-bottom: 1.5px dotted var(--blue); height: 1px; margin-bottom: 3px; }
  .appointment__field--date { left: 150px; top: 72px; }
  .appointment__field--date::after { width: 130px; }
  .appointment__field--time { left: 350px; top: 26px; }
  .appointment__field--time::after { width: 130px; }

  /* ---------- Front: contact ---------- */
  .card--front { left: 600px; top: 380px; background: var(--white); }

  .card--front .brand { left: 60px; top: 110px; color: var(--blue); }
  .card--front .brand__dot { background: var(--blue); }
  .card--front .brand__name { font-size: 38px; }

  .person { position: absolute; right: 30px; top: 42px; font-family: "Tinos", serif; color: var(--blue); }
  .person__head { display: flex; align-items: center; gap: 6px; }
  .person__icon { width: 26px; height: 26px; flex: none; }
  .person__name { font-weight: 700; font-size: 21px; }
  .person__role {
    display: flex; align-items: center; gap: 6px; justify-content: flex-end;
    color: var(--grey); font-size: 13px; margin-top: -2px;
  }
  .person__role::before { content: ""; width: 60px; border-top: 1px solid var(--grey); }
  .person__creds { color: var(--grey); font-weight: 700; font-size: 12.5px; margin-top: 3px; padding-left: 30px; }

  .contact {
    position: absolute; left: 356px; top: 134px;
    list-style: none; font-family: "Tinos", serif; color: var(--ink);
    font-size: 13px; line-height: 17px;
  }
  .contact li { display: flex; gap: 7px; align-items: flex-start; }
  .contact svg { width: 12px; height: 12px; margin-top: 2px; flex: none; fill: var(--blue); }
</style>
</head>
<body>

  <!-- Back of card -->
  <section class="card card--back">
    <svg class="card__shape" viewBox="0 0 540 300" aria-hidden="true">
      <path d="M0 300 V250 C0 218 22 206 68 204 C210 198 360 184 458 170 C512 162 540 150 540 118 V300 Z" fill="var(--white)"/>
    </svg>

    <div class="brand">
      <span class="brand__dot"></span>
      <span class="brand__name"><span class="brand__line">Bluewren</span><span class="brand__line">Podiatry</span></span>
    </div>

    <ul class="services">
      <li>general podiatry for all ages</li>
      <li>corns and callus treatment</li>
      <li>Ingrown toenails &amp; nail surgery</li>
      <li>Forefoot, arch and heel pain</li>
      <li>Gait analysis</li>
      <li>Sports Podiatry and Orthotics</li>
      <li>Paediatric Assessments</li>
      <li>Diabetes Foot Assessment</li>
    </ul>

    <div class="appointment">
      <div class="appointment__title">Next appointment,</div>
      <div class="appointment__field appointment__field--date">Date</div>
      <div class="appointment__field appointment__field--time">Time</div>
    </div>
  </section>

  <!-- Front of card -->
  <section class="card card--front">
    <svg class="card__shape" viewBox="0 0 540 300" aria-hidden="true">
      <rect x="0" y="0" width="540" height="7" fill="var(--blue)"/>
      <path d="M0 46 C110 72 220 52 330 0 H380 C250 62 120 96 0 70 Z" fill="var(--grey)"/>
      <path d="M0 36 C110 60 220 40 320 0 H336 C230 50 115 74 0 46 Z" fill="var(--blue)"/>
      <path d="M0 300 V266 C0 246 14 238 40 242 C200 250 360 236 490 222 C522 219 540 206 540 190 V300 Z" fill="var(--blue)"/>
    </svg>

    <div class="brand">
      <span class="brand__dot"></span>
      <span class="brand__name"><span class="brand__line">Bluewren</span><span class="brand__line">Podiatry</span></span>
    </div>

    <div class="person">
      <div class="person__head">
        <svg class="person__icon" viewBox="0 0 26 26" aria-hidden="true">
          <circle cx="13" cy="13" r="13" fill="var(--grey)"/>
          <circle cx="13" cy="9.5" r="4" fill="var(--white)"/>
          <path d="M6 21 C6 15.5 20 15.5 20 21 Z" fill="var(--white)"/>
        </svg>
        <span class="person__name">Marisol Tenbury</span>
      </div>
      <div class="person__role">Podiatrist</div>
      <div class="person__creds">M.Pod.P., B.Hlth. Sci, MFLsoc</div>
    </div>

    <ul class="contact">
      <li>
        <svg viewBox="0 0 12 12" aria-hidden="true"><circle cx="6" cy="6" r="6"/><path d="M3.6 3 L5 2.8 L5.6 4.4 L4.8 5 C5.2 6 6 6.8 7 7.2 L7.6 6.4 L9.2 7 L9 8.4 C6 8.6 3.4 6 3.6 3 Z" fill="#fff"/></svg>
        <span>(03) 9416 2738</span>
      </li>
      <li>
        <svg viewBox="0 0 12 12" aria-hidden="true"><circle cx="6" cy="6" r="6"/><rect x="3" y="5" width="6" height="4" fill="#fff"/><rect x="4" y="3" width="4" height="2" fill="#fff"/></svg>
        <span>(03) 9523 4178</span>
      </li>
      <li>
        <svg viewBox="0 0 12 12" aria-hidden="true"><path d="M6 0 C2.8 0 1.5 2.2 1.5 4.2 C1.5 7 6 12 6 12 C6 12 10.5 7 10.5 4.2 C10.5 2.2 9.2 0 6 0 Z"/><circle cx="6" cy="4.3" r="1.6" fill="#fff"/></svg>
        <span>58 Coleby St,<br>Marrowdale North Vic,<br>3164</span>
      </li>
    </ul>
  </section>

</body>
</html>
```